Visitenkarten-Design für Sonnen-/Fensterschutz
Zielgruppe
KLW GmbH ist eine Firma, die Sonnenschutz und Fensterschutz anbieten.
'Ihr kompetenter Partner in Sachen Sonnenschutz- , Fenster- und Türtechnik. Sie erhalten echtes Handwerk aus dem Mühlviertel zu fairen Preisen.'
Unsere Zielgruppe sind Personen mit Haus, die am Land leben.
Firmenname: KLW GmbH
Slogan: Fenster & Sonnenschutz
Aufgabenstellung
Hier befindet sich das Logodesign: https://dx.qv/t-QwLpo7RbNs
Bitte ein schlichtes Design bereitstellen mit einer Dummy-Person:
Jonas Weidlinger + Telefonnummer + Email
Die finalen Daten bitte erst am Schluss berücksichtigen (für Gewinnerdesign)
Gerne auch hintern + vorne bedruckbar bereitstellen.

```html
<!DOCTYPE html>
<html lang="de">
<head>
<meta charset="utf-8">
<title>KLW GmbH – Visitenkarte</title>
<link href="https://fonts.googleapis.com/css2?family=Ubuntu:wght@400;500;700&family=Open+Sans:wght@400;700&display=swap" rel="stylesheet">
<style>
  :root {
    --bg: #ecebe8;
    --card-white: #ffffff;
    --card-grey: #e9e9e9;
    --red: #d62828;
    --red-deep: #b81f1f;
    --orange: #e8742f;
    --orange-light: #f08a4b;
    --ink: #1c1c1c;
    --ink-soft: #333333;
  }
  * { box-sizing: border-box; margin: 0; padding: 0; }
  html, body { width: 1200px; height: 800px; overflow: hidden; }
  body {
    background: var(--bg);
    font-family: "Open Sans", sans-serif;
    display: flex;
    align-items: center;
    justify-content: center;
    gap: 50px;
  }
  .card {
    position: relative;
    width: 525px;
    height: 300px;
    overflow: hidden;
    box-shadow: 0 10px 30px rgba(0,0,0,0.18);
  }

  /* Front */
  .card--front {
    background: linear-gradient(135deg, var(--card-white) 40%, var(--card-grey) 100%);
  }
  .front-brand {
    position: absolute;
    left: 34px;
    top: 96px;
    display: flex;
    align-items: center;
    gap: 7px;
    font-family: "Ubuntu", sans-serif;
    font-weight: 700;
    font-size: 15px;
    color: var(--red);
  }
  .brand-square {
    width: 12px; height: 12px;
    background: var(--red);
  }
  .front-divider {
    position: absolute;
    left: 138px;
    top: 66px;
    width: 2px;
    height: 92px;
    background: var(--red);
    transform: rotate(22deg);
  }
  .person {
    position: absolute;
    left: 166px;
    top: 66px;
    font-family: "Ubuntu", sans-serif;
  }
  .person-name {
    font-size: 30px;
    font-weight: 500;
    color: var(--red);
    line-height: 1.1;
  }
  .person-role {
    font-size: 26px;
    font-weight: 400;
    color: var(--ink);
    line-height: 1.2;
  }
  .contact-list {
    position: absolute;
    left: 300px;
    top: 160px;
    list-style: none;
    font-size: 14px;
    color: var(--ink-soft);
  }
  .contact-list li {
    display: flex;
    align-items: center;
    gap: 9px;
    margin-bottom: 7px;
  }
  .contact-list .contact-web { font-weight: 700; color: var(--ink); }
  .contact-icon { width: 13px; height: 13px; flex: none; }
  .front-band {
    position: absolute;
    left: 0;
    bottom: 0;
    width: 160px;
    height: 26px;
    background: linear-gradient(180deg, var(--orange-light), var(--orange));
  }
  .front-panel {
    position: absolute;
    left: 160px;
    bottom: 0;
    width: 118px;
    height: 120px;
    background: linear-gradient(180deg, var(--red) 70%, var(--orange) 100%);
    display: flex;
    align-items: center;
    justify-content: center;
    gap: 6px;
    font-family: "Ubuntu", sans-serif;
    font-weight: 700;
    font-size: 17px;
    color: var(--card-white);
  }
  .front-panel .brand-square { background: var(--card-white); width: 10px; height: 10px; }

  /* Back */
  .card--back {
    background: linear-gradient(120deg, var(--orange-light) 0%, var(--orange) 40%, var(--red) 80%, var(--red-deep) 100%);
    display: flex;
    align-items: center;
    justify-content: center;
  }
  .back-brand {
    display: flex;
    align-items: center;
    gap: 12px;
    font-family: "Ubuntu", sans-serif;
    font-weight: 700;
    font-size: 44px;
    color: var(--card-white);
  }
  .back-brand .brand-square { background: var(--card-white); width: 26px; height: 26px; }
</style>
</head>
<body>

  <section class="card card--front" aria-label="Visitenkarte Vorderseite">
    <div class="front-brand"><span class="brand-square"></span>KLW GmbH</div>
    <div class="front-divider"></div>
    <div class="person">
      <p class="person-name">Jonas Weidlinger</p>
      <p class="person-role">Director</p>
    </div>
    <ul class="contact-list">
      <li>
        <svg class="contact-icon" viewBox="0 0 16 16"><rect x="4" y="1" width="8" height="14" rx="1.5" fill="#d62828"/><rect x="5.5" y="3" width="5" height="8" fill="#fff"/></svg>
        0111 4826301558
      </li>
      <li>
        <svg class="contact-icon" viewBox="0 0 16 16"><rect x="1" y="3" width="14" height="10" fill="#d62828"/><path d="M1 3 L8 9 L15 3" fill="none" stroke="#fff" stroke-width="1.3"/></svg>
        jonas@beispielseite.de
      </li>
      <li class="contact-web">
        <svg class="contact-icon" viewBox="0 0 16 16"><circle cx="8" cy="8" r="7" fill="#d62828"/><g fill="none" stroke="#fff" stroke-width="1"><ellipse cx="8" cy="8" rx="3" ry="6.5"/><line x1="1.5" y1="8" x2="14.5" y2="8"/></g></svg>
        www.beispielseite.de
      </li>
    </ul>
    <div class="front-band"></div>
    <div class="front-panel"><span class="brand-square"></span>KLW GmbH</div>
  </section>

  <section class="card card--back" aria-label="Visitenkarte Rückseite">
    <div class="back-brand"><span class="brand-square"></span>KLW GmbH</div>
  </section>

</body>
</html>
```